Wrenfield Pharmacy opening

We want to have a double sided 5.5"x8.5" flyer for a new Pharmacy opening in a well known strip mall in the neighborhood and we are planning to mail it to neighbors homes.

Want to put the outside pharmacy picture on the main side of the flyer and a coupon with 25% off towards an OTC product on the back in addition to the info below (preferably in a sort of bulletin points not a list (something like the 2 examples attached).

Colors to be red like the exterior sign and blue like the interior wall paint:

Front side should have:
Wrenfield pharmacy
Your locally owned and operated pharmacy around the corner.
317-4821 Ostrander rd.
Pike hollow plaza
T. 555 206 3379 (call or text)
F. 555-206-3381

Free prescription delivery
Text us for refills
Specialized compounding
Customized compression stockings

The back side should have:

Do you forget taking your medications! We offer multiple compliance packaging options at no additional cost.
Had shingles before or worried to have it? travelling soon? check our vaccinations options!
Suffering side effects? We are experienced to check your medications interactions & different coverage options.
Hard time monitoring your blood pressure? Trying to stop smoking? we can always help.

FEELING BETTER STARTS HERE

```html
<!DOCTYPE html>
<html lang="en">
<head>
<meta charset="utf-8">
<title>Wrenfield Pharmacy – Opening Mailer</title>
<link rel="stylesheet" href="https://fonts.googleapis.com/css2?family=Open+Sans:ital,wght@0,400;0,600;0,700;0,800;1,700;1,800&family=Roboto+Condensed:wght@700&display=swap">
<style>
  :root{
    --red:#e3202a;
    --navy:#2f3f5f;
    --navy-dark:#24324d;
    --white:#ffffff;
    --page:#eceef1;
    --line:#b9bec6;
  }
  *{box-sizing:border-box;margin:0;padding:0}
  html,body{width:1200px;height:1101px;overflow:hidden;background:var(--page)}
  body{font-family:"Open Sans",Arial,sans-serif;position:relative}
  .card{position:absolute;left:210px;width:780px;height:505px;background:var(--white);overflow:hidden;box-shadow:0 4px 14px rgba(0,0,0,.18)}
  .card--front{top:30px}
  .card--back{top:565px}
  .card-art{position:absolute;inset:0}
  .brand{position:absolute;display:flex;align-items:center;gap:12px}
  .brand-mark{border-radius:50%;background:var(--red);flex:none}
  .brand-name{color:var(--red);font-weight:800;text-transform:uppercase;line-height:1.05}
  .front-brand{left:28px;top:24px}
  .front-brand .brand-mark{width:92px;height:92px}
  .front-brand .brand-name{font-size:25px}
  .tagline{position:absolute;left:32px;top:128px;width:330px;color:var(--navy);font-weight:700;font-size:19px;line-height:1.3}
  .now-open{position:absolute;left:28px;top:196px;color:var(--white);font-weight:800;font-size:42px;letter-spacing:1px;line-height:50px}
  .services{position:absolute;left:26px;top:262px;list-style:none}
  .services li{display:flex;align-items:center;gap:10px;height:40px;color:var(--white);font-weight:700;font-size:17px}
  .bullet{width:30px;height:30px;border-radius:50%;background:var(--red);border:2px solid rgba(255,255,255,.8);display:flex;align-items:center;justify-content:center;flex:none}
  .contact-strip{position:absolute;left:24px;top:468px;display:flex;align-items:center;gap:12px;color:var(--white);font-family:"Roboto Condensed",Arial,sans-serif;font-weight:700;font-size:21px;letter-spacing:.3px}
  .address-front{position:absolute;right:14px;top:474px;color:var(--navy);font-weight:600;font-size:13px;white-space:nowrap}
  .offer-badge{position:absolute;left:465px;top:340px;width:112px;height:112px;border-radius:50%;background:var(--red);color:var(--white);text-align:center;display:flex;flex-direction:column;justify-content:center}
  .offer-badge strong{font-family:"Roboto Condensed",Arial,sans-serif;font-weight:700;font-size:27px;line-height:1}
  .offer-badge span{font-size:11px;font-weight:700;line-height:1.25;margin-top:4px}

  .back-brand{left:26px;top:14px}
  .back-brand .brand-mark{width:56px;height:56px}
  .back-brand .brand-name{font-size:18px}
  .concerns{position:absolute;left:22px;top:92px;width:330px;list-style:none}
  .concerns li{display:flex;gap:12px;margin-bottom:13px}
  .concern-icon{width:26px;flex:none;padding-top:2px}
  .concern-title{color:var(--red);font-weight:700;font-size:11.5px;line-height:1.2}
  .concern-text{color:var(--white);font-size:10.5px;line-height:1.3}
  .slogan{position:absolute;left:26px;top:306px;color:var(--white);font-weight:800;font-style:italic;font-size:19px;letter-spacing:.2px;white-space:nowrap}
  .coupon{position:absolute;left:26px;top:342px;width:282px;height:104px;background:var(--red);border-radius:14px;padding:4px}
  .coupon-inner{display:flex;height:100%;background:var(--white);border:2px dashed var(--navy);border-radius:11px;overflow:hidden}
  .coupon-text{width:150px;display:flex;flex-direction:column;justify-content:center;align-items:center;color:var(--red);font-weight:800}
  .coupon-text strong{font-size:30px;line-height:1}
  .coupon-text span{font-size:12px;margin-top:6px;letter-spacing:.3px}
  .coupon-photo{flex:1}
  .pharmacist-photo{position:absolute;left:334px;top:300px;width:124px;height:205px;border-radius:56px 56px 0 0}
  .back-strip{position:absolute;left:24px;top:466px;display:flex;align-items:center;gap:12px;color:var(--white);font-family:"Roboto Condensed",Arial,sans-serif;font-weight:700;font-size:21px}
  .mail-address{position:absolute;left:470px;top:44px;color:#333;font-size:13px;line-height:1.45}
  .mail-address strong{color:var(--red);font-weight:700;display:block}
  .stamp-box{position:absolute;left:650px;top:40px;width:96px;height:78px;border:1.5px solid var(--line)}
  .write-line{position:absolute;left:500px;width:246px;height:1.5px;background:var(--line)}
</style>
</head>
<body>

<section class="card card--front" aria-label="Mailer front">
  <svg class="card-art" viewBox="0 0 780 505" width="780" height="505">
    <defs>
      <linearGradient id="storefront" x1="0" y1="0" x2="1" y2="1">
        <stop offset="0" stop-color="#8f8a86"/>
        <stop offset=".35" stop-color="#b5625c"/>
        <stop offset=".6" stop-color="#d9d9dc"/>
        <stop offset="1" stop-color="#7b8aa6"/>
      </linearGradient>
    </defs>
    <rect x="0" y="238" width="780" height="230" fill="var(--navy)"/>
    <path d="M0 192 L300 186 L312 236 L0 246 Z" fill="var(--red)"/>
    <path d="M426 0 C352 140 380 350 560 440" fill="none" stroke="var(--navy)" stroke-width="10"/>
    <path d="M448 0 C376 140 404 340 574 430" fill="none" stroke="var(--red)" stroke-width="9"/>
    <path d="M468 0 C398 140 424 330 586 424 L780 420 L780 0 Z" fill="url(#storefront)" role="img" aria-label="Photo of the pharmacist and a customer in front of the pharmacy storefront with its red sign"/>
    <path d="M0 462 L470 455 Q500 456 500 480 L500 505 L0 505 Z" fill="var(--red)"/>
    <path d="M500 505 L500 470 Q504 455 520 454 L780 448 L780 505 Z" fill="var(--white)"/>
  </svg>

  <div class="brand front-brand">
    <span class="brand-mark"></span>
    <span class="brand-name">Wrenfield<br>Pharmacy</span>
  </div>
  <p class="tagline">Your locally owned and operated pharmacy around the corner.</p>
  <p class="now-open">NOW OPEN</p>

  <ul class="services">
    <li><span class="bullet"><svg width="16" height="12" viewBox="0 0 16 12"><rect x="0" y="1" width="10" height="7" fill="#fff"/><path d="M10 3h3l3 3v2h-6z" fill="#fff"/><circle cx="4" cy="10" r="1.8" fill="#fff"/><circle cx="12" cy="10" r="1.8" fill="#fff"/></svg></span>Free prescription delivery</li>
    <li><span class="bullet"><svg width="16" height="14" viewBox="0 0 16 14"><path d="M1 1h14v9H6l-4 3v-3H1z" fill="#fff"/></svg></span>Text us for refills</li>
    <li><span class="bullet"><svg width="14" height="14" viewBox="0 0 14 14"><path d="M1 6h12l-2 7H3z" fill="#fff"/><rect x="6" y="0" width="2" height="7" fill="#fff" transform="rotate(25 7 3)"/></svg></span>Specialized compounding</li>
    <li><span class="bullet"><svg width="12" height="16" viewBox="0 0 12 16"><path d="M3 0h5v9l3 4v3H4l-1-4z" fill="#fff"/></svg></span>Customized compression stockings</li>
  </ul>

  <div class="offer-badge"><strong>25% OFF</strong><span>towards an<br>OTC product</span></div>

  <div class="contact-strip">
    <span>CALL OR TEXT</span>
    <svg width="18" height="24" viewBox="0 0 18 24"><rect x="2" y="1" width="14" height="22" rx="3" fill="none" stroke="#fff" stroke-width="2.5"/><circle cx="9" cy="19" r="1.5" fill="#fff"/></svg>
    <span>555 206 3379 &nbsp;F. 555-206-3381</span>
  </div>
  <p class="address-front">317-4821 Ostrander rd. Pike hollow plaza</p>
</section>

<section class="card card--back" aria-label="Mailer back">
  <svg class="card-art" viewBox="0 0 780 505" width="780" height="505">
    <path d="M0 78 L330 92 C420 120 470 260 462 505 L0 505 Z" fill="var(--navy)"/>
    <path d="M350 60 C450 100 500 260 476 470" fill="none" stroke="var(--navy)" stroke-width="4"/>
    <path d="M368 60 C472 100 520 260 494 470" fill="none" stroke="var(--red)" stroke-width="6"/>
    <path d="M0 458 L330 452 Q350 452 352 470 L354 505 L0 505 Z" fill="var(--red)"/>
  </svg>

  <div class="brand back-brand">
    <span class="brand-mark"></span>
    <span class="brand-name">Wrenfield<br>Pharmacy</span>
  </div>

  <ul class="concerns">
    <li>
      <svg class="concern-icon" viewBox="0 0 26 18" height="18"><rect x="1" y="4" width="14" height="9" rx="4.5" fill="none" stroke="#fff" stroke-width="1.6"/><rect x="10" y="4" width="14" height="9" rx="4.5" fill="none" stroke="#fff" stroke-width="1.6"/></svg>
      <div><p class="concern-title">Do you forget taking your medications!</p><p class="concern-text">We offer multiple compliance packaging options at no additional cost.</p></div>
    </li>
    <li>
      <svg class="concern-icon" viewBox="0 0 26 24" height="24"><rect x="7" y="5" width="12" height="17" rx="2" fill="#fff"/><rect x="10" y="1" width="6" height="4" fill="none" stroke="#fff" stroke-width="1.5"/></svg>
      <div><p class="concern-title">Had shingles before or worried to have it?</p><p class="concern-text">Travelling Soon? Check Our Vaccinations Options!</p></div>
    </li>
    <li>
      <svg class="concern-icon" viewBox="0 0 26 24" height="24"><rect x="4" y="2" width="14" height="18" fill="#fff"/><circle cx="19" cy="18" r="5" fill="#fff" stroke="var(--navy)" stroke-width="1.5"/><path d="M16.5 18l2 2 3-3.5" fill="none" stroke="var(--navy)" stroke-width="1.5"/></svg>
      <div><p class="concern-title">Suffering side effects?</p><p class="concern-text">We are experienced to check your medications interactions &amp; different coverage options.</p></div>
    </li>
    <li>
      <svg class="concern-icon" viewBox="0 0 26 24" height="24"><path d="M6 2v7a5 5 0 0 0 10 0V2" fill="none" stroke="#fff" stroke-width="1.6"/><path d="M11 14v4a4 4 0 0 0 8 0v-3" fill="none" stroke="#fff" stroke-width="1.6"/><circle cx="19" cy="13" r="2" fill="none" stroke="#fff" stroke-width="1.5"/></svg>
      <div><p class="concern-title">Hard time monitoring your blood pressure?</p><p class="concern-text">Trying to stop smoking? we can always help.</p></div>
    </li>
  </ul>

  <p class="slogan">FEELING BETTER STARTS HERE</p>

  <div class="coupon">
    <div class="coupon-inner">
      <div class="coupon-text"><strong>25% OFF</strong><span>FOR OTC PRODUCT</span></div>
      <div class="coupon-photo" role="img" aria-label="Photo of the pharmacy shelves stocked with over-the-counter products" style="background:linear-gradient(160deg,#e4e8ee,#b49a84)"></div>
    </div>
  </div>

  <div class="pharmacist-photo" role="img" aria-label="Photo of a smiling pharmacist in a white coat with arms crossed" style="background:linear-gradient(180deg,#8a6a52 0%,#d8b49a 35%,#f3f4f6 55%,#ffffff 100%)"></div>

  <div class="back-strip">
    <span>CALL OR TEXT</span>
    <svg width="18" height="24" viewBox="0 0 18 24"><rect x="2" y="1" width="14" height="22" rx="3" fill="none" stroke="#fff" stroke-width="2.5"/><circle cx="9" cy="19" r="1.5" fill="#fff"/></svg>
    <span>555 206 3379</span>
  </div>

  <p class="mail-address"><strong>Wrenfield pharmacy</strong>317-4821 Ostrander rd.<br>Pike hollow plaza</p>
  <div class="stamp-box"></div>
  <div class="write-line" style="top:190px"></div>
  <div class="write-line" style="top:232px"></div>
  <div class="write-line" style="top:274px"></div>
  <div class="write-line" style="top:316px"></div>
</section>

</body>
</html>
```